Car Spare Parts Packaging Box

I need a packaging design for car spare parts, specifically electrical parts or motor electric, such as fuel pump, motor power window, switch power window, motor fan radiator, sensor oxygen, starter, alternator, etc.

Our logo is as attached. Slogan "Premium Quality Auto Parts".
Font:
BinnerD (company name)
MictrogrammaDMedExt (slogan)

Color:
Blue - the gradients consist of C100 M100 Y0 K0 / C100 M0 Y0 K0
Yellow - gradients consist of C16 M32 Y100 K61 / C0 M0 Y100 K0

For reference:
VORTEK (multi products), Kravo (fuel pump, sensor oxygen), Tollan (multi product)
Updates

Project Deadline Extended
Reason: Dear all, I still haven't find one suit my chemistry. Please browse existing worldwide brand from Japan and germany for more references. Since i am abroad at the moment, i will inform you more existing brand by tomorrow.

Project Deadline Extended
Reason: For some designers to finalize their work.

Industry/Entity Type

Electrical

Font styles to use
Serif
Sans Serif

Colors
0555a3
0892cd

Requirements
Must have
• 1. Space at one of the sides for label.
2. Gradient color design
3. Less white background.
Vortek n tollan as main reference.
Nice to have
• wording: some of below options.
durable
reliable
high quality
best quality
quality guaranteed
replacement parts
long life
spare parts silhouette / blue print / real picture
Should not have
• 1. should not have car draw/picture, since we are selling car spare parts, not the car itself.
2. do not use common font: arial, times new roman.
Expect a new unique font.

```html
<!DOCTYPE html>
<html lang="en">
<head>
<meta charset="utf-8">
<title>Halvern Fuel Pump Packaging</title>
<link rel="stylesheet" href="https://fonts.googleapis.com/css2?family=Michroma&family=Russo+One&display=swap">
<style>
  :root {
    --page: #f4f5f7;
    --blue-deep: #1b2596;
    --blue-mid: #0555a3;
    --blue-bright: #0892cd;
    --gold-dark: #5e4f0c;
    --gold-light: #c9b400;
    --yellow: #f2e21a;
    --slogan: #e4da98;
    --white: #ffffff;
    --pump-dark: #1d1a2c;
    --pump-light: #5b5670;
  }
  * { margin: 0; padding: 0; box-sizing: border-box; }
  html, body { width: 1200px; height: 1000px; overflow: hidden; background: var(--page); }
  .canvas { position: relative; width: 1200px; height: 1000px; }

  .top-panel, .end-panel, .front-panel {
    position: absolute; overflow: hidden;
    background: linear-gradient(160deg, var(--blue-deep) 0%, var(--blue-mid) 40%, var(--blue-bright) 100%);
  }
  .top-panel { left: 350px; top: 50px; width: 820px; height: 300px; }
  .end-panel { left: 30px; top: 370px; width: 300px; height: 480px; padding: 60px 30px; color: var(--white); }
  .front-panel { left: 350px; top: 370px; width: 820px; height: 480px; }

  .gold-band {
    position: absolute; left: 0; top: 0; width: 70px; height: 100%;
    background: linear-gradient(90deg, var(--gold-dark), var(--gold-light) 60%, var(--gold-dark));
  }

  /* end panel */
  .end-title { font-family: "Michroma", sans-serif; font-size: 20px; line-height: 1.3; color: #bfe6f7; }
  .end-contact { margin-top: 34px; font-family: "Michroma", sans-serif; font-size: 13px; line-height: 1.9; color: #d4eefa; }
  .end-small { margin-top: 22px; font-family: "Michroma", sans-serif; font-size: 9px; line-height: 1.8; color: #a9d8ee; }
  .end-badges { position: absolute; left: 30px; bottom: 60px; display: flex; gap: 12px; }
  .end-badges span { width: 26px; height: 26px; border: 2px solid #bfe6f7; border-radius: 4px; }

  /* shared brand + features */
  .brand { position: absolute; display: flex; align-items: center; }
  .brand-mark { background: var(--yellow); }
  .brand-name { font-family: "Russo One", sans-serif; color: var(--white); line-height: 1; }
  .brand-sub { position: absolute; font-family: "Michroma", sans-serif; color: var(--white); letter-spacing: 2px; white-space: nowrap; }
  .features { position: absolute; list-style: none; }
  .features li { font-family: "Russo One", sans-serif; color: var(--yellow); transform: skewX(-8deg); white-space: nowrap; }
  .features li::before { content: "• "; }
  .product-image { position: absolute; background: linear-gradient(180deg, var(--pump-light), var(--pump-dark)); }

  /* top panel */
  .top-panel .product-image { left: 110px; top: 30px; width: 380px; height: 130px; border-radius: 65px; }
  .top-panel .brand { left: 180px; top: 195px; gap: 12px; }
  .top-panel .brand-mark { width: 34px; height: 34px; }
  .top-panel .brand-name { font-size: 40px; }
  .top-panel .brand-sub { left: 226px; top: 242px; font-size: 9px; }
  .top-panel .features { left: 540px; top: 70px; }
  .top-panel .features li { font-size: 21px; line-height: 1.45; }

  /* front panel */
  .slogan {
    position: absolute; left: 110px; top: 34px;
    font-family: "Michroma", sans-serif; font-size: 28px; color: var(--slogan); letter-spacing: 1px;
  }
  .front-panel .brand { left: 320px; top: 100px; gap: 14px; }
  .front-panel .brand-mark { width: 44px; height: 44px; }
  .front-panel .brand-name { font-size: 54px; }
  .front-panel .brand-sub { left: 378px; top: 160px; font-size: 11px; }
  .front-panel .product-image { left: 110px; top: 200px; width: 390px; height: 190px; border-radius: 95px; }
  .front-panel .features { left: 520px; top: 215px; }
  .front-panel .features li { font-size: 25px; line-height: 1.45; }
  .product-name {
    position: absolute; left: 420px; top: 410px;
    font-family: "Michroma", sans-serif; font-size: 22px; color: var(--yellow);
  }
</style>
</head>
<body>
<main class="canvas">
  <section class="top-panel">
    <div class="gold-band"></div>
    <div class="product-image" role="img" aria-label="Photograph of an electric fuel pump"></div>
    <div class="brand">
      <span class="brand-mark"></span>
      <span class="brand-name">HALVERN</span>
    </div>
    <p class="brand-sub">PREMIUM QUALITY AUTO PARTS</p>
    <ul class="features">
      <li>Quality Guaranteed</li>
      <li>German Technology</li>
      <li>Best Aftermarket</li>
    </ul>
  </section>

  <section class="end-panel">
    <p class="end-title">Premium Quality<br>Auto Parts</p>
    <p class="end-contact">1-800-420-7716<br>www.halvern.com</p>
    <p class="end-small">Quality Tested<br>Part FP-2018</p>
    <div class="end-badges"><span></span><span></span><span></span></div>
  </section>

  <section class="front-panel">
    <div class="gold-band"></div>
    <p class="slogan">Premium Quality Auto Parts</p>
    <div class="brand">
      <span class="brand-mark"></span>
      <span class="brand-name">HALVERN</span>
    </div>
    <p class="brand-sub">PREMIUM QUALITY AUTO PARTS</p>
    <div class="product-image" role="img" aria-label="Photograph of an electric fuel pump"></div>
    <ul class="features">
      <li>Quality Guaranteed</li>
      <li>German Technology</li>
      <li>Best Aftermarket</li>
    </ul>
    <p class="product-name">Fuel Pump</p>
  </section>
</main>
</body>
</html>
```